International business needs business cards

Our company, DRV Ventures Inc. is in the business of supplying a range construction products with particular emphasis on CEMENT. We have developed our own brand - TORVAN SUPPLIES - with which to infiltrate the market. We are launching our brand of cement (TORVAN Type IS Cement) into the Caribbean which is unlike anything this market has ever seen. A monopoly has existed here for the past 60-odd years and the market has now opened to allow the importation of other brands and consumers are anxious and ready for change/improvement. We are very excited to be launching and want to make a great first impression. We will be conducting workshops and seminars (from government level to the hardware store owners) and we want our business card to give us the strong, confident introduction that we need.

Target Market(s)

construction; builders; engineers; home owners

Industry/Entity Type

Construction

Contact Information for Business Card

Marisol Depree
CEO
cell # 1 555 4180736
Ground floor,Lindell Plaza Suite 2734
George Town,Grand Cayman
Cayman Islands,KY1-4823
EMAIL: m.depree@drvventuresinc.example
web site drvventuresinc.example

COMPANY: skype info drv.ventures.example

second card
Yvette Brannock-Depree
CFO
CELL# 1 555 607 3941
George Town,Grand Cayman
Cayman Islands,KY1-4823
EMAIL: y.brannockdepree@drvventuresinc.example
website drvventuresinc.example

Requirements
Must have
• Business cards must display BOTH logos - DRV is the company and TORVAN is the brand.

```html
<!DOCTYPE html>
<html lang="en">
<head>
<meta charset="utf-8">
<title>DRV Ventures Inc. — Business Card</title>
<link rel="stylesheet" href="https://fonts.googleapis.com/css2?family=Source+Sans+3:wght@400;600;700&display=swap">
<style>
  :root {
    --backdrop: #1c1c1c;
    --card: #ffffff;
    --brand-red: #7e1517;
    --ink: #1a1a1a;
    --text: #222222;
  }
  * { margin: 0; padding: 0; box-sizing: border-box; }
  html, body { width: 1200px; height: 900px; overflow: hidden; }
  body {
    background: var(--backdrop);
    font-family: "Source Sans 3", Arial, sans-serif;
    position: relative;
  }
  .card {
    position: absolute;
    top: 170px;
    width: 347px;
    height: 561px;
    background: var(--card);
  }
  .card--front { left: 259px; }
  .card--back { left: 631px; }
  .band {
    position: absolute;
    left: 102px;
    width: 143px;
    background: var(--brand-red);
  }
  .band--top { top: 0; height: 30px; }
  .band--bottom { bottom: 0; height: 28px; }

  .company-mark {
    position: absolute;
    display: flex;
    align-items: center;
    gap: 14px;
  }
  .card--front .company-mark { top: 105px; left: 60px; }
  .card--back .company-mark { top: 136px; left: 59px; }
  .company-mark__square {
    width: 92px; height: 92px;
    background: var(--brand-red);
    flex: none;
  }
  .company-mark__name {
    font-weight: 700;
    font-size: 32px;
    line-height: 1.05;
    color: var(--ink);
  }

  .contact {
    position: absolute;
    top: 248px;
    left: 0;
    width: 100%;
    text-align: center;
    color: var(--text);
    font-size: 15.5px;
    line-height: 20px;
  }
  .contact__name {
    color: var(--brand-red);
    font-weight: 600;
    font-size: 19px;
    line-height: 24px;
  }
  .contact__title { margin-bottom: 18px; }
  .contact__address { margin-bottom: 18px; }
  .contact__line {
    display: flex;
    justify-content: center;
    align-items: center;
    gap: 7px;
  }
  .contact__line svg { width: 11px; height: 11px; fill: var(--brand-red); flex: none; }

  .brand-mark {
    position: absolute;
    top: 290px;
    left: 0;
    width: 100%;
    display: flex;
    flex-direction: column;
    align-items: center;
    gap: 14px;
  }
  .brand-mark__circle {
    width: 84px; height: 84px;
    border-radius: 50%;
    background: #3a3a3a;
  }
  .brand-mark__name {
    font-weight: 700;
    font-size: 22px;
    letter-spacing: 2px;
    color: #3a3a3a;
  }
</style>
</head>
<body>
  <section class="card card--front">
    <div class="band band--top"></div>
    <div class="company-mark">
      <div class="company-mark__square"></div>
      <div class="company-mark__name">DRV<br>Ventures Inc.</div>
    </div>
    <div class="contact">
      <p class="contact__name">Marisol Depree</p>
      <p class="contact__title">CEO</p>
      <p class="contact__address">Ground floor, Lindell Plaza Suite<br>2734 George Town, Grand Cayman<br>Cayman Islands, KY1-4823</p>
      <p class="contact__line">
        <svg viewBox="0 0 12 12" aria-hidden="true"><path d="M3 0h6a1 1 0 0 1 1 1v10a1 1 0 0 1-1 1H3a1 1 0 0 1-1-1V1a1 1 0 0 1 1-1zm0 1.5v8h6v-8z"/></svg>
        1 555 4180736
      </p>
      <p class="contact__line">
        <svg viewBox="0 0 12 12" aria-hidden="true"><path d="M0 2h12v8H0zm1 1l5 3.5L11 3z"/></svg>
        m.depree@drvventuresinc.example
      </p>
      <p class="contact__line">
        <svg viewBox="0 0 12 12" aria-hidden="true"><circle cx="6" cy="6" r="6"/><path d="M1 6h10M6 0v12" stroke="#fff" stroke-width="1"/></svg>
        www.drvventuresinc.example
      </p>
    </div>
    <div class="band band--bottom"></div>
  </section>

  <section class="card card--back">
    <div class="company-mark">
      <div class="company-mark__square"></div>
      <div class="company-mark__name">DRV<br>Ventures Inc.</div>
    </div>
    <div class="brand-mark">
      <div class="brand-mark__circle"></div>
      <div class="brand-mark__name">TORVAN SUPPLIES</div>
    </div>
  </section>
</body>
</html>
```